Bring me business with this creative business card

Design my new business card. I am looking for something different with an impact. People will take a look at this card & they will 1- see how different & creative I am, 2-understand what I do 3- Call me to meet me!

I make videos with a message, testimonials. I am dynamic, fun, creative & human. My new website is in construction but in the meantime you can check this old one: brightpath.ca & another one Tidebloom.com & tidebloom facebook page.
I make videos. sometimes with a cameraman, sometimes with my phone. As an ex Public Relations agent, the message is the most important thing for me. I want to make my clients shine! When they start with me they often remind me of a lamb, when I finish coaching them they are powerful like LIONS! That's why I need a powerful business card!

Target Market(s)

Entrepreneurs, solo entrepreneurs, small & medium companies & start ups. People i will meet while networking. People that need videos on their website & social Networks to get attention, to be visible. men & women. From 35 to 49 years old.
I am an ex Public relations agent. I used to send clients in traditional medias, now with videos they have more chances to be seen on google the new media. I do videos of the president, his team, his loyal clients saying how great the company is & expert videos like series so people can be seen for example every 1 st of every month with a short 2 minute video. Also with my 20 years in marketing & communications I can coach & give tips to anybody who needs it.
Target: anybody who would like my old website brightpath.ca & I also have another website but it will be off line soon: tidebloom.com could give you ideas.

Industry/Entity Type

Communications

Contact Information for Business Card

I am in Montreal,So the business cards have to be the usual size like we have in Montreal: 9 cm x 5 cm
Details:My text: Mathilde Tessier Communication coach/HEAD OF VIDEO. "Videos that let your story shine" off: 514-555-0147 cell: 514-555-0183. tidebloom.com
mathilde@tidebloom.com logo facebook, youtube, instagram

Colors
f37122

Requirements
Must have
• Dynamic, happy. Orange. Be creative in the look but NOT the shape of the card. Easy to read. Big enough to read.
Should not have
• No funny shapes: no round, no square, just the usual. I love creative but NOT on shape.

```html
<!DOCTYPE html>
<html lang="en">
<head>
<meta charset="utf-8">
<title>Tidebloom business card</title>
<link rel="stylesheet" href="https://fonts.googleapis.com/css2?family=Cinzel:wght@700&family=Roboto:wght@400;500&family=Roboto+Condensed:wght@400;500&display=swap">
<style>
  :root {
    --backdrop: #2b2b2b;
    --card-orange: #f3a623;
    --brand-orange: #f06a22;
    --accent-red: #ef5a24;
    --accent-yellow: #f5a71d;
    --paper: #f3f3f3;
    --ink: #4a4a4a;
    --white: #ffffff;
  }
  * { margin: 0; padding: 0; box-sizing: border-box; }
  html, body { width: 1200px; height: 960px; overflow: hidden; }
  body { background: var(--backdrop); position: relative; font-family: "Roboto", sans-serif; }

  .card { position: absolute; left: 320px; width: 600px; height: 344px; overflow: hidden; }

  /* Front */
  .card-front { top: 108px; background: var(--card-orange); }
  .front-artwork {
    position: absolute; left: 0; top: 0; width: 295px; height: 344px;
    background: linear-gradient(160deg, #f58a1f 0%, #f7b21a 45%, #fbd40e 70%, #f47a20 100%);
    clip-path: polygon(0 0, 88% 0, 96% 30%, 100% 55%, 86% 78%, 72% 100%, 0 100%);
  }
  .front-brand {
    position: absolute; left: 318px; width: 262px; top: 208px; text-align: center; color: var(--white);
  }
  .front-brand .wordmark {
    font-family: "Cinzel", serif; font-weight: 700; font-size: 36px; letter-spacing: 1px; line-height: 1;
  }
  .tagline {
    display: flex; align-items: center; justify-content: center; gap: 8px; white-space: nowrap;
    font-family: "Roboto Condensed", sans-serif; font-size: 15px; letter-spacing: 0.3px; margin-top: 7px;
  }
  .tagline::before, .tagline::after { content: ""; width: 34px; height: 1px; background: currentColor; }
  .front-brand .slogan { font-size: 14px; margin-top: 3px; white-space: nowrap; }

  /* Back */
  .card-back { top: 493px; background: var(--paper); }
  .back-brand { position: absolute; left: 84px; width: 188px; top: 86px; text-align: center; color: var(--brand-orange); }
  .brand-dot { width: 86px; height: 86px; border-radius: 50%; background: var(--accent-yellow); margin: 0 auto 18px; }
  .back-brand .wordmark { font-family: "Cinzel", serif; font-weight: 700; font-size: 27px; line-height: 1; letter-spacing: 0.5px; white-space: nowrap; }
  .back-brand .tagline { font-size: 11px; margin-top: 5px; color: var(--accent-yellow); }
  .back-brand .tagline::before, .back-brand .tagline::after { width: 22px; }

  .divider { position: absolute; left: 289px; top: 90px; width: 1px; height: 154px; background: linear-gradient(transparent, #9a9a9a, transparent); }

  .contact { position: absolute; left: 315px; top: 92px; }
  .contact .name { font-family: "Roboto Condensed", sans-serif; font-weight: 500; font-size: 24px; color: var(--accent-red); line-height: 1.1; }
  .contact .role { font-family: "Roboto", sans-serif; font-weight: 500; font-size: 15px; color: var(--accent-yellow); line-height: 19px; margin-top: 4px; }
  .contact ul { list-style: none; margin-top: 14px; }
  .contact li { display: flex; align-items: center; gap: 8px; font-size: 14px; color: var(--ink); line-height: 19.5px; }
  .contact svg { width: 13px; height: 13px; fill: var(--accent-red); flex: none; }

  .band-red { position: absolute; left: 0; bottom: 0; width: 390px; height: 15px; background: var(--accent-red); }
  .band-web {
    position: absolute; right: 0; bottom: 0; width: 232px; height: 32px; background: var(--accent-yellow);
    clip-path: polygon(32px 0, 100% 0, 100% 100%, 0 100%);
    color: var(--white); font-size: 14px; letter-spacing: 1px; line-height: 32px; padding-left: 58px;
  }
</style>
</head>
<body>
  <section class="card card-front">
    <div class="front-artwork" role="img" aria-label="Low-poly geometric lion illustration in orange and yellow"></div>
    <div class="front-brand">
      <div class="wordmark">TIDEBLOOM</div>
      <div class="tagline">1 STORY 1 VOICE</div>
      <div class="slogan">Videos that let your story shine</div>
    </div>
  </section>

  <section class="card card-back">
    <div class="back-brand">
      <div class="brand-dot"></div>
      <div class="wordmark">TIDEBLOOM</div>
      <div class="tagline">1 STORY 1 VOICE</div>
    </div>
    <div class="divider"></div>
    <div class="contact">
      <div class="name">MATHILDE T.</div>
      <div class="role">COMMUNICATION COACH<br>HEAD OF VIDEO</div>
      <ul>
        <li><svg viewBox="0 0 24 24"><path d="M6.6 10.8a15 15 0 0 0 6.6 6.6l2.2-2.2a1 1 0 0 1 1-.25 11.4 11.4 0 0 0 3.6.57 1 1 0 0 1 1 1V20a1 1 0 0 1-1 1A17 17 0 0 1 3 4a1 1 0 0 1 1-1h3.5a1 1 0 0 1 1 1c0 1.25.2 2.45.57 3.57a1 1 0 0 1-.25 1z"/></svg>514-555-0147</li>
        <li><svg viewBox="0 0 24 24"><path d="M7 1h10a2 2 0 0 1 2 2v18a2 2 0 0 1-2 2H7a2 2 0 0 1-2-2V3a2 2 0 0 1 2-2zm0 3v14h10V4z"/></svg>514-555-0183.</li>
        <li><svg viewBox="0 0 24 24"><path d="M2 5h20v14H2zm2 2v.5l8 5 8-5V7l-8 5z"/></svg>mathilde@tidebloom.com</li>
      </ul>
    </div>
    <div class="band-red"></div>
    <div class="band-web">www.tidebloom.com</div>
  </section>
</body>
</html>
```